Simple and Clean business card design

We would like the design to be simple clean and to incorporate our colors.

We are open to your design and talent, we have the dots in our logo as we think of it as data points and we connect data points for people.

We are open to see the great creative and clean design you bring to the table

Contact Information for Business Card

please include: name, position, email, phone and website

Font styles to use
Sans Serif

Requirements
Must have
• my colors incorporated, simplicity
Nice to have
• lots of white space, simplicity
Should not have
• complexicity/ complex art

```html
<!DOCTYPE html>
<html lang="en">
<head>
<meta charset="utf-8">
<title>Dotlane Business Card</title>
<link rel="stylesheet" href="https://fonts.googleapis.com/css2?family=Ubuntu:wght@500&family=Roboto:wght@400&family=Montserrat:wght@600&display=swap">
<style>
  :root {
    --backdrop: #676565;
    --brand-blue: #4285f4;
    --paper: #ffffff;
    --paper-tint: #f3f6fd;
    --ink: #0e0e0e;
  }
  html, body {
    margin: 0;
    padding: 0;
    width: 1200px;
    height: 801px;
    overflow: hidden;
    background: var(--backdrop);
  }
  .canvas {
    position: relative;
    width: 1200px;
    height: 801px;
  }
  .card {
    position: absolute;
    top: 274px;
    width: 443px;
    height: 263px;
    overflow: hidden;
  }
  .card--front { left: 153px; background: var(--brand-blue); }
  .card--back { left: 625px; background: var(--ink); }
  .card__art {
    position: absolute;
    inset: 0;
    width: 443px;
    height: 263px;
  }
  .contact {
    position: absolute;
    left: 22px;
    top: 76px;
    color: var(--paper);
  }
  .contact__name {
    margin: 0;
    font-family: "Ubuntu", sans-serif;
    font-size: 19px;
    font-weight: 500;
    line-height: 1;
  }
  .contact__role {
    margin: 2px 0 0;
    font-family: "Roboto", sans-serif;
    font-size: 12.5px;
    font-weight: 400;
    line-height: 1.1;
  }
  .contact__list {
    list-style: none;
    margin: 21px 0 0;
    padding: 0;
    font-family: "Roboto", sans-serif;
    font-size: 12.5px;
    line-height: 18px;
  }
  .contact__item {
    display: flex;
    align-items: center;
    gap: 3px;
  }
  .contact__icon { width: 16px; height: 16px; flex: none; }
  .wordmark {
    position: absolute;
    display: flex;
    align-items: center;
    font-family: "Montserrat", sans-serif;
    font-weight: 600;
    letter-spacing: -0.5px;
    line-height: 1;
  }
  .wordmark--front {
    right: 24px;
    bottom: 22px;
    font-size: 29px;
    color: var(--ink);
    gap: 6px;
  }
  .wordmark--back {
    left: 0;
    right: 0;
    top: 108px;
    justify-content: center;
    font-size: 52px;
    color: var(--paper);
    gap: 10px;
  }
  .wordmark__dot { border-radius: 50%; background: var(--brand-blue); flex: none; }
  .wordmark--front .wordmark__dot { width: 10px; height: 10px; }
  .wordmark--back .wordmark__dot { width: 15px; height: 15px; }
</style>
</head>
<body>
<main class="canvas">
  <section class="card card--front" aria-label="Business card front">
    <svg class="card__art" viewBox="0 0 443 263" role="img" aria-label="Decorative area for the brand's coloured data-point circles">
      <defs>
        <linearGradient id="art-fill" x1="0" y1="0" x2="1" y2="1">
          <stop offset="0" stop-color="var(--paper-tint)"/>
          <stop offset="1" stop-color="var(--paper)"/>
        </linearGradient>
      </defs>
      <path d="M312 0 H443 V263 H177 C172 240 185 222 200 212 C180 190 178 150 205 118 C220 100 225 90 220 70 C215 35 260 5 312 0 Z" fill="url(#art-fill)"/>
    </svg>

    <div class="contact">
      <h1 class="contact__name">Nora Vance</h1>
      <p class="contact__role">Founder/ CEO</p>
      <ul class="contact__list">
        <li class="contact__item">
          <svg class="contact__icon" viewBox="0 0 16 16" aria-hidden="true">
            <circle cx="8" cy="8" r="7" fill="none" stroke="currentColor" stroke-width="1.3"/>
            <path d="M5.2 4.6c.6-.5 1.1-.3 1.4.3l.5 1c.2.4 0 .8-.3 1l-.4.3c.4.9 1 1.6 1.9 2l.3-.4c.3-.3.7-.4 1-.2l1 .6c.5.3.6.8.2 1.3-.7.9-1.7 1-2.9.3-1.3-.8-2.3-1.9-2.9-3.2-.5-1.2-.4-2.3.2-3z" fill="currentColor"/>
          </svg>
          <span>555-014-2290</span>
        </li>
        <li class="contact__item">
          <svg class="contact__icon" viewBox="0 0 16 16" aria-hidden="true">
            <circle cx="8" cy="8" r="7" fill="none" stroke="currentColor" stroke-width="1.3"/>
            <rect x="4.3" y="5.5" width="7.4" height="5" fill="currentColor"/>
            <path d="M4.3 5.5 8 8.4l3.7-2.9" fill="none" stroke="var(--brand-blue)" stroke-width="0.8"/>
          </svg>
          <span>nora.vance@dotlane.one</span>
        </li>
        <li class="contact__item">
          <svg class="contact__icon" viewBox="0 0 16 16" aria-hidden="true">
            <circle cx="8" cy="8" r="7" fill="none" stroke="currentColor" stroke-width="1.3"/>
            <g fill="none" stroke="currentColor" stroke-width="0.8">
              <circle cx="8" cy="8" r="4"/>
              <ellipse cx="8" cy="8" rx="1.8" ry="4"/>
              <path d="M4 8h8M4.6 6h6.8M4.6 10h6.8"/>
            </g>
          </svg>
          <span>www.Dotlane.one</span>
        </li>
      </ul>
    </div>

    <div class="wordmark wordmark--front">
      <span class="wordmark__dot"></span>
      <span class="wordmark__name">Dotlane</span>
    </div>
  </section>

  <section class="card card--back" aria-label="Business card back">
    <div class="wordmark wordmark--back">
      <span class="wordmark__dot"></span>
      <span class="wordmark__name">Dotlane</span>
    </div>
  </section>
</main>
</body>
</html>
```